BOLD & MINIMALIST DESIGN NEEDED

We want a very bold but minimalistic business card design that is impactful and utilizes both sides of the business card. Our current logo is included for your use.

We want bold fonts and good use of negative space. We don't want the logo to overpower the design.

Target Market(s)

Professionals who are building new commercial buildings.

Industry/Entity Type

Construction

Contact Information for Business Card

Name, Title, email, office phone, cell phone, website

Font styles to use
Serif
Sans Serif

Requirements
Must have
• Bold design!

```html
<!DOCTYPE html>
<html lang="en">
<head>
<meta charset="utf-8">
<title>Ridgeway Design + Build — Business Card</title>
<link rel="stylesheet" href="https://fonts.googleapis.com/css2?family=Arimo:wght@400;700&display=swap">
<style>
  :root {
    --bg: #e6e6e6;
    --white: #ffffff;
    --ink: #0b0c0d;
    --green: #86c332;
    --green-light: #b4dc7a;
    --green-deep: #7fbf2a;
    --text-light: #f4f4f4;
  }
  * { box-sizing: border-box; margin: 0; padding: 0; }
  html, body {
    width: 1200px; height: 1200px; overflow: hidden;
    background: var(--bg);
    font-family: "Arimo", Arial, sans-serif;
  }
  .card {
    position: absolute; left: 255px;
    width: 690px; height: 394px;
    overflow: hidden;
  }
  .card--front { top: 160px; background: var(--white); }
  .card--back {
    top: 652px;
    background: radial-gradient(ellipse at 50% 50%, var(--green-light) 0%, var(--green) 60%, var(--green-deep) 100%);
  }

  /* front: brand area */
  .brand {
    position: absolute; left: 0; top: 0; width: 100%; height: 232px;
    display: flex; align-items: center; justify-content: center; gap: 16px;
  }
  .brand__mark { width: 22px; height: 22px; background: var(--green); }
  .brand__name {
    color: var(--ink); font-weight: 700; text-align: center; line-height: 1;
  }
  .brand__name .line1 { display: block; font-size: 46px; letter-spacing: 0.01em; }
  .brand__name .line2 { display: block; font-size: 16px; letter-spacing: 0.42em; margin-top: 8px; }

  .accent-band { position: absolute; left: 0; top: 232px; width: 100%; height: 5px; background: var(--green); }

  .info-panel {
    position: absolute; left: 0; top: 240px; width: 100%; height: 154px;
    background: var(--ink);
  }
  .person {
    position: absolute; right: 370px; top: 52px; text-align: right;
  }
  .person__name { color: var(--green); font-weight: 700; font-size: 27px; line-height: 1; }
  .person__title { color: var(--text-light); font-size: 16px; margin-top: 7px; }
  .divider {
    position: absolute; left: 336px; top: 30px; width: 1px; height: 96px;
    background: #7a7a7a;
  }
  .contacts {
    position: absolute; left: 352px; top: 35px; list-style: none;
  }
  .contacts li {
    display: flex; align-items: center; gap: 10px;
    color: var(--text-light); font-size: 17.5px; line-height: 20.5px;
  }
  .contacts svg { width: 14px; height: 14px; fill: var(--green); flex: none; }

  /* back */
  .back-brand {
    position: absolute; inset: 0;
    display: flex; align-items: center; justify-content: center; gap: 22px;
  }
  .back-brand__mark { width: 34px; height: 34px; background: var(--ink); }
  .back-brand__name {
    color: var(--ink); font-weight: 700; line-height: 1; text-align: center;
  }
  .back-brand__name .line1 { display: block; font-size: 72px; }
  .back-brand__name .line2 { display: block; font-size: 24px; letter-spacing: 0.42em; margin-top: 12px; }
</style>
</head>
<body>

<section class="card card--front">
  <div class="brand">
    <span class="brand__mark"></span>
    <div class="brand__name">
      <span class="line1">RIDGEWAY</span>
      <span class="line2">DESIGN + BUILD</span>
    </div>
  </div>
  <div class="accent-band"></div>
  <div class="info-panel">
    <div class="person">
      <div class="person__name">DANIEL REYES</div>
      <div class="person__title">President</div>
    </div>
    <div class="divider"></div>
    <ul class="contacts">
      <li>
        <svg viewBox="0 0 16 16" aria-hidden="true"><path d="M3.6 1.2l2.2 2.6-1.3 1.8c.9 2 2.4 3.6 4.4 4.6l1.8-1.3 2.6 2.2-1.4 2.4C7 13.2 2.6 8.6 1.4 2.6z"/></svg>
        555-210-4830
      </li>
      <li>
        <svg viewBox="0 0 16 16" aria-hidden="true"><path d="M4 0h8v16H4zM5.5 2v10h5V2zM7 13.2h2v1.4H7z" fill-rule="evenodd"/></svg>
        555-318-7724
      </li>
      <li>
        <svg viewBox="0 0 16 16" aria-hidden="true"><path d="M1 3h14v10H1zM2.5 4.5v.4L8 9l5.5-4.1v-.4zM2.5 6.8v4.7h11V6.8L8 10.9z" fill-rule="evenodd"/></svg>
        info@ridgewaybuild.com
      </li>
      <li>
        <svg viewBox="0 0 16 16" aria-hidden="true"><circle cx="8" cy="8" r="7.5"/><path d="M4 4.5c1.5-.5 2.5.5 2 2s1.5 1.5 1 3-1.5 2-1 3.5M10 3c-.5 1.5 1 2 2 2.5" stroke="#0b0c0d" stroke-width="1.2" fill="none"/></svg>
        www.ridgewaybuild.com
      </li>
    </ul>
  </div>
</section>

<section class="card card--back">
  <div class="back-brand">
    <span class="back-brand__mark"></span>
    <div class="back-brand__name">
      <span class="line1">RIDGEWAY</span>
      <span class="line2">DESIGN + BUILD</span>
    </div>
  </div>
</section>

</body>
</html>
```